Small Business Broker Business Card Design

A business card design for a small business brokerage, which is a financial service, not unlike real estate brokerage, but for small businesses such as laundromats, pizza shops, restaurants, cleaners etc. The designs should all be simple, more conservative in nature, using the colors and font of the logo. Again, think real estate Brokerage as a business context
Contact Information for Business Card
Name: Glen R. Harlow. Title: Small Business Advisor. Email: g.harlow@bayfieldcapitalworks.example. Mobile: (555) 274-3918. Office: (555) 806-2147. www.bayfieldcapitalworks.example

```html
<!DOCTYPE html>
<html lang="en">
<head>
<meta charset="utf-8">
<title>Bayfield Capital Works — Business Card</title>
<link rel="stylesheet" href="https://fonts.googleapis.com/css2?family=Montserrat:wght@700;800&family=Arimo:wght@400&display=swap">
<style>
  :root {
    --bg: #1b1c1b;
    --paper: #ffffff;
    --green: #7dbb2f;
    --green-dark: #5f9a22;
    --green-light: #94cf45;
    --navy: #1b3a6b;
    --grey: #6b6b6b;
  }
  * { margin: 0; padding: 0; box-sizing: border-box; }
  html, body { width: 1200px; height: 963px; overflow: hidden; background: var(--bg); }
  .canvas { position: relative; width: 1200px; height: 963px; }

  .card {
    position: absolute; left: 250px; width: 700px; height: 400px;
    border-radius: 26px; overflow: hidden;
  }
  .card--front { top: 50px; background: var(--paper); }
  .card--back { top: 513px; background: var(--green); }

  .holder { position: absolute; left: 56px; top: 48px; }
  .holder__name {
    font-family: "Montserrat", sans-serif; font-weight: 800;
    font-size: 34px; color: var(--green); text-transform: uppercase; letter-spacing: 0.5px;
  }
  .holder__title {
    font-family: "Arimo", sans-serif; font-size: 19px; color: var(--grey); margin-top: 2px;
  }

  .contacts { position: absolute; left: 56px; top: 158px; list-style: none; }
  .contacts li {
    display: flex; align-items: center; gap: 12px;
    font-family: "Arimo", sans-serif; font-size: 18px; color: var(--grey); height: 28px;
  }
  .contacts svg { width: 16px; height: 16px; flex: none; }

  .brand { position: absolute; right: 44px; top: 118px; text-align: right; }
  .brand__name {
    font-family: "Montserrat", sans-serif; font-weight: 800; font-size: 21px;
    color: var(--navy); text-transform: uppercase; letter-spacing: 1px; white-space: nowrap;
  }
  .brand__tagline {
    font-family: "Montserrat", sans-serif; font-weight: 700; font-size: 10px;
    color: var(--green); text-transform: uppercase; letter-spacing: 1.6px; margin-top: 4px;
    white-space: nowrap;
  }

  .stripes { position: absolute; left: 0; bottom: 0; width: 700px; height: 400px; }

  .back__texture { position: absolute; inset: 0;
    background: linear-gradient(135deg, var(--green-light), var(--green) 50%, var(--green-dark)); }
  .back__brand { position: absolute; left: 0; right: 0; top: 168px; text-align: center; }
  .back__name {
    font-family: "Montserrat", sans-serif; font-weight: 800; font-size: 30px;
    color: var(--paper); text-transform: uppercase; letter-spacing: 1.5px;
  }
  .back__tagline {
    font-family: "Montserrat", sans-serif; font-weight: 700; font-size: 12px;
    color: var(--paper); text-transform: uppercase; letter-spacing: 2.4px; margin-top: 6px;
  }
</style>
</head>
<body>
<main class="canvas">
  <section class="card card--front" aria-label="Business card front">
    <div class="holder">
      <h1 class="holder__name">Glen R. Harlow</h1>
      <p class="holder__title">Small Business Advisor</p>
    </div>

    <ul class="contacts">
      <li>
        <svg viewBox="0 0 16 16"><path d="M4 1.5l2.4 3-1.3 1.6a8 8 0 0 0 4.8 4.8l1.6-1.3 3 2.4-1.5 2.4C7.5 14.5 1.5 8.5 1.6 3z" fill="var(--green)"/></svg>
        (555) 806-2147
      </li>
      <li>
        <svg viewBox="0 0 16 16"><rect x="4" y="1" width="8" height="14" rx="1.5" fill="none" stroke="var(--green)" stroke-width="1.6"/><circle cx="8" cy="12.5" r="0.9" fill="var(--green)"/></svg>
        (555) 274-3918
      </li>
      <li>
        <svg viewBox="0 0 16 16"><rect x="1" y="3.5" width="14" height="9" fill="none" stroke="var(--green)" stroke-width="1.6"/><path d="M1.5 4l6.5 5 6.5-5" fill="none" stroke="var(--green)" stroke-width="1.6"/></svg>
        g.harlow@bayfieldcapitalworks.example
      </li>
      <li>
        <svg viewBox="0 0 16 16"><circle cx="8" cy="8" r="6.5" fill="none" stroke="var(--green)" stroke-width="1.4"/><ellipse cx="8" cy="8" rx="3" ry="6.5" fill="none" stroke="var(--green)" stroke-width="1.2"/><path d="M1.5 8h13M2.5 5h11M2.5 11h11" stroke="var(--green)" stroke-width="1.1"/></svg>
        www.bayfieldcapitalworks.example
      </li>
    </ul>

    <div class="brand">
      <p class="brand__name">Bayfield Capital Works, Inc</p>
      <p class="brand__tagline">Sound guidance for every business sale</p>
    </div>

    <svg class="stripes" viewBox="0 0 700 400" aria-hidden="true">
      <polyline points="0,282 400,282 470,400" fill="none" stroke="var(--navy)" stroke-width="11"/>
      <polyline points="0,302 392,302 452,400" fill="none" stroke="var(--green)" stroke-width="5"/>
      <polyline points="0,316 384,316 438,400" fill="none" stroke="var(--green)" stroke-width="2.5"/>
    </svg>
  </section>

  <section class="card card--back" aria-label="Business card back">
    <div class="back__texture" role="img" aria-label="Embossed repeating brand pattern on green"></div>
    <div class="back__brand">
      <p class="back__name">Bayfield Capital Works, Inc</p>
      <p class="back__tagline">Sound guidance for every business sale</p>
    </div>
  </section>
</main>
</body>
</html>
```